Automotive Accessories Business Card

Design a business template that match our new logo design and our industry.

https://www.qelmotorgear.com/

Target Market(s)

Aftermarket auto parts and accessories

Industry/Entity Type

automotive

Contact Information for Business Card

company logo

Font styles to use
Serif
Sans Serif

Colors
EB3D1F
EC4F4E
F09395
F8D3D4
FCEDEE

```html
<!DOCTYPE html>
<html lang="en">
<head>
<meta charset="utf-8">
<title>QEL Motor Gear – Business Card</title>
<link href="https://fonts.googleapis.com/css2?family=Arimo:wght@400;700&display=swap" rel="stylesheet">
<style>
  :root{
    --stage:#858585;
    --card-light:#fcfbfc;
    --card-dark:#434143;
    --brand-red:#d91f26;
    --ink:#1a1a1a;
    --white:#ffffff;
  }
  *{margin:0;padding:0;box-sizing:border-box}
  html,body{width:1075px;height:1200px;overflow:hidden}
  body{background:var(--stage);font-family:"Arimo",Arial,sans-serif;position:relative}
  .card{position:absolute;left:205px;width:663px;height:395px;box-shadow:3px 3px 2px #222}
  .card--front{top:187px;background:var(--card-light)}
  .card--back{top:637px;background:var(--card-dark)}
  .side-band{position:absolute;left:0;top:0;width:62px;height:100%;background:var(--card-dark)}
  .race-strip{position:absolute;left:62px;top:0;width:24px;height:100%;
    background:linear-gradient(90deg,#f3f0f0 0 50%,var(--brand-red) 50% 100%)}
  .brand{position:absolute;display:flex;align-items:center;gap:12px;font-weight:700;letter-spacing:1px;white-space:nowrap}
  .brand__square{width:22px;height:22px;background:var(--brand-red)}
  .card--front .brand{right:56px;top:92px;font-size:32px;color:var(--card-dark)}
  .card--back .brand{left:50%;top:50%;transform:translate(-50%,-50%);font-size:46px;color:var(--white)}
  .card--back .brand__square{width:32px;height:32px}
  .details{position:absolute;left:106px;top:185px;color:var(--ink)}
  .details__name{font-size:25px;font-weight:700;color:var(--brand-red);line-height:1}
  .details__title{font-size:18px;line-height:1.1;margin-top:1px}
  .details__address{font-size:17.5px;line-height:23px;margin-top:15px}
  .contacts{list-style:none;margin-top:23px;font-size:17.5px;line-height:23.5px}
  .contacts li{display:flex;align-items:center;gap:6px}
  .contacts svg{width:17px;height:17px;flex:none}
  .accent{color:var(--brand-red)}
</style>
</head>
<body>
  <section class="card card--front">
    <div class="side-band"></div>
    <div class="race-strip" role="img" aria-label="Red and white checkered racing strip"></div>
    <div class="brand"><span class="brand__square"></span>QEL MOTOR GEAR</div>
    <div class="details">
      <h1 class="details__name">MARCUS HALE</h1>
      <p class="details__title">Managing Director</p>
      <p class="details__address">421, Address line goes here<br>45452,Country Name</p>
      <ul class="contacts">
        <li><svg viewBox="0 0 24 24" fill="none" stroke="#d91f26" stroke-width="2.4" stroke-linecap="round"><path d="M5 3h4l2 5-2.5 1.5a11 11 0 0 0 6 6L16 13l5 2v4a2 2 0 0 1-2 2A17 17 0 0 1 3 5a2 2 0 0 1 2-2z"/></svg>044-123 456 789</li>
        <li><svg viewBox="0 0 24 24"><rect x="2" y="5" width="20" height="14" fill="#d91f26"/><path d="M2 5l10 8 10-8M2 19l7-7M22 19l-7-7" stroke="#fff" stroke-width="1.6" fill="none"/></svg>info@webname.com</li>
        <li><svg viewBox="0 0 24 24" fill="none" stroke="#d91f26" stroke-width="2"><circle cx="12" cy="12" r="9.5"/><ellipse cx="12" cy="12" rx="4" ry="9.5"/><path d="M2.5 12h19M4 7h16M4 17h16"/></svg>www.<span class="accent">qelmotorgear</span>.com</li>
      </ul>
    </div>
  </section>
  <section class="card card--back">
    <div class="brand"><span class="brand__square"></span>QEL MOTOR GEAR</div>
  </section>
</body>
</html>
```